Car transport business

We need a new business card design. Attached is our old card sample. I would just like to adjust the logo colors (blue and red) to be brighter. I changed my name to the brighter red and the word dispatcher to a brighter blue as an example. But you can adjust those colors further. And then perhaps you can use the same colors for the card design but use your imagination.

As a suggestion so the card stands out I would like to add a clip art of car carrier truck. Attached are examples of that as well

```html
<!DOCTYPE html>
<html lang="en">
<head>
<meta charset="utf-8">
<title>Northline Carriers — Business Card</title>
<link href="https://fonts.googleapis.com/css2?family=Arimo:wght@400;700&display=swap" rel="stylesheet">
<style>
  :root {
    --backdrop: #1e1e1e;
    --card: #0b0b0b;
    --brand-blue: #1f7ad6;
    --brand-red: #ee1c2a;
    --ink-light: #e6e6e6;
    --ink-muted: #bdbdbd;
    --rule: #7a7a7a;
  }
  * { box-sizing: border-box; margin: 0; padding: 0; }
  html, body { width: 1200px; height: 900px; overflow: hidden; }
  body {
    background: var(--backdrop);
    font-family: "Arimo", Arial, sans-serif;
    display: flex;
    align-items: center;
    justify-content: center;
    gap: 60px;
  }
  .card {
    width: 525px;
    height: 300px;
    background: var(--card);
    border-radius: 22px;
    position: relative;
    box-shadow: 0 14px 34px rgba(0,0,0,.55);
  }
  .brand {
    display: flex;
    align-items: center;
    gap: 12px;
  }
  .brand-dot {
    width: 34px; height: 34px;
    border-radius: 50%;
  }
  .brand-name {
    font-weight: 700;
    font-size: 30px;
    letter-spacing: 1px;
    text-transform: uppercase;
  }
  .tagline {
    font-size: 10px;
    letter-spacing: 3px;
    text-transform: uppercase;
    margin-top: 6px;
    padding-left: 46px;
  }

  /* front */
  .card-front .brand-block { position: absolute; left: 40px; top: 38px; }
  .card-front .brand-dot { background: var(--brand-blue); }
  .card-front .brand-name { color: var(--brand-red); }
  .card-front .tagline { color: var(--brand-blue); }
  .person { position: absolute; left: 86px; top: 138px; }
  .person-name {
    font-weight: 700;
    font-size: 26px;
    text-transform: uppercase;
    letter-spacing: .5px;
  }
  .person-name .first { color: var(--brand-blue); }
  .person-name .last { color: var(--brand-red); }
  .person-title {
    color: var(--ink-light);
    font-size: 14px;
    letter-spacing: 1px;
    margin-top: 4px;
  }
  .divider {
    width: 92px; height: 1px;
    background: var(--rule);
    margin: 12px 0 12px 0;
  }
  .contacts { list-style: none; }
  .contacts li {
    display: flex; align-items: center; gap: 10px;
    color: var(--ink-light);
    font-size: 15px;
    line-height: 22px;
  }
  .contacts svg { width: 16px; height: 16px; fill: var(--brand-blue); flex: none; }

  /* back */
  .card-back {
    display: flex; flex-direction: column;
    align-items: center; justify-content: center;
  }
  .card-back .brand-dot { background: var(--ink-light); }
  .card-back .brand-name { color: var(--ink-light); }
  .card-back .tagline { color: var(--ink-muted); }
</style>
</head>
<body>

  <section class="card card-front" aria-label="Card front">
    <div class="brand-block">
      <div class="brand">
        <span class="brand-dot"></span>
        <span class="brand-name">Northline Carriers</span>
      </div>
      <p class="tagline">The auto transport professionals</p>
    </div>

    <div class="person">
      <h1 class="person-name"><span class="first">Ravi</span> <span class="last">Lendon</span></h1>
      <p class="person-title">DISPATCHER</p>
      <div class="divider"></div>
      <ul class="contacts">
        <li>
          <svg viewBox="0 0 24 24" aria-hidden="true"><path d="M6.6 10.8a15.1 15.1 0 0 0 6.6 6.6l2.2-2.2a1 1 0 0 1 1-.25 11.4 11.4 0 0 0 3.6.57 1 1 0 0 1 1 1V20a1 1 0 0 1-1 1A17 17 0 0 1 3 4a1 1 0 0 1 1-1h3.5a1 1 0 0 1 1 1c0 1.25.2 2.45.57 3.57a1 1 0 0 1-.25 1z"/></svg>
          555-210-4178
        </li>
        <li>
          <svg viewBox="0 0 24 24" aria-hidden="true"><path d="M6 2h10l2 2v5H6zM4 10h16a2 2 0 0 1 2 2v6h-4v4H6v-4H2v-6a2 2 0 0 1 2-2zm4 7v3h8v-3z"/></svg>
          555-210-4190
        </li>
        <li>
          <svg viewBox="0 0 24 24" aria-hidden="true"><path d="M2 5h20v14H2zm2 2v.5l8 5 8-5V7zm0 2.9V17h16V9.9l-8 5z"/></svg>
          dispatch@northlinecarriers.com
        </li>
      </ul>
    </div>
  </section>

  <section class="card card-back" aria-label="Card back">
    <div class="brand">
      <span class="brand-dot"></span>
      <span class="brand-name">Northline Carriers</span>
    </div>
    <p class="tagline">The auto transport professionals</p>
  </section>

</body>
</html>
```